Web Design Project

The aim of this project to design a website for a service that would offer services for small business and non profit organizations using opensource software that is weaved to work together in harmony.

The website name is: vestolia.net

Vestolia in Arabic means: cabbage. Cabbage is composed of leaves, actually there is nothing except leaves. Each leave by itself is not called cabbage, but a collection of leaves that are organized in a central way would give us cabbage.

Same idea for Vestolia where open source software very well organized and integrated would create a new thing with a new value.

Target Market(s)

Small business, Europe, Africa, Far east and Middle east

Industry/Entity Type

Small Business

Requirements
Must have
• The website would offer the following sections:
* Home page
* Benefits: value of vestolia
* Applications: applications offered by vestolia
* Pricing
* Purchase
* Customer log in
* Support
- FAQ
- Knowledge base
- Forums
- Open tickets

Please take the following consideration in design:
* White should predominate
* Only black and the colors of logo are permitted (attched)
Nice to have
• Design is better to express:
* Openness
* Dynamic
* Usable
* Cost effective

```html
<!DOCTYPE html>
<html lang="en">
<head>
<meta charset="utf-8">
<title>Vestolia</title>
<link href="https://fonts.googleapis.com/css2?family=Open+Sans:wght@400;600;700&display=swap" rel="stylesheet">
<style>
:root{
  --green:#7dc225;
  --blue:#2a9fd6;
  --ink:#1e1e1e;
  --panel:#f0f0f0;
  --white:#ffffff;
  --footer:#525252;
  --cal-dark:#2b2c2e;
  --cal-head:#1f2022;
  --muted:#8a8a8a;
  --photo-a:#e9eaec;
  --photo-b:#9a9ca3;
}
*{box-sizing:border-box;margin:0;padding:0}
html,body{width:809px;height:1200px;overflow:hidden}
body{position:relative;background:var(--white);font-family:"Open Sans",Arial,sans-serif;color:var(--ink)}
.hero{position:absolute;left:0;top:0;width:809px;height:296px;background:linear-gradient(180deg,var(--photo-a) 0%,#c9cbd0 55%,var(--photo-b) 100%)}
.brand{position:absolute;left:38px;top:110px;display:flex;align-items:center;gap:12px}
.brand-mark{width:34px;height:34px;border-radius:50%;background:var(--green)}
.brand-name{font-size:46px;font-weight:600;color:var(--ink);letter-spacing:.5px}
.login{position:absolute;left:630px;top:53px;width:146px;height:160px;background:var(--white);border-radius:4px;box-shadow:0 2px 6px rgba(0,0,0,.2);padding:12px 9px;font-size:8px}
.login h2{font-size:9px;font-weight:700;text-align:center;margin-bottom:14px}
.field{height:22px;background:#ececec;border-bottom:1px solid #dcdcdc;padding:3px 6px;color:#333}
.field.pass{height:20px;letter-spacing:1px;font-size:9px}
.signin{margin-top:16px;height:22px;background:var(--green);color:var(--white);font-weight:700;text-align:center;line-height:22px;font-size:9px}
.login-foot{display:flex;justify-content:space-between;margin-top:8px;font-size:7px}
.login-foot span:first-child::before{content:"";display:inline-block;width:6px;height:6px;background:#e3e3e3;margin-right:6px;vertical-align:-1px}
.nav{position:absolute;left:0;top:296px;width:809px;height:40px;background:var(--green)}
.nav a{position:absolute;top:0;line-height:40px;font-size:12px;color:var(--ink);text-decoration:none;transform:translateX(-50%)}
.nav a.active{top:6px;left:104px;width:102px;height:27px;line-height:27px;background:#f4f4f4;border-radius:3px;text-align:center}
.welcome{position:absolute;left:44px;top:358px;width:722px;height:330px;background:var(--panel);border-radius:3px;padding:17px 24px 0 24px}
.welcome h1{font-size:20px;font-weight:400;color:var(--blue);text-align:center;margin-bottom:11px}
.welcome p{font-size:11.2px;line-height:15px;text-indent:62px;margin-bottom:7px;padding:0 0 0 0}
.feeds{position:absolute;left:47px;top:732px;width:722px;height:251px;background:var(--panel);border-radius:3px}
.feeds h2{position:absolute;top:24px;font-size:17px;font-weight:400;color:var(--blue);transform:translateX(-50%)}
.divider{position:absolute;left:345px;top:25px;width:1px;height:202px;background:#9a9a9a}
.card{position:absolute;top:65px;height:154px;background:var(--white);box-shadow:0 0 8px rgba(0,0,0,.08);font-size:11.5px;line-height:16px}
.scroll{position:absolute;right:6px;top:10px;width:5px;height:125px;background:#bdbdbd;border-radius:3px}
.scroll::before{content:"";position:absolute;left:0;top:0;width:5px;height:46px;background:#2e2e2e;border-radius:3px}
.news{left:41px;width:275px;padding:16px 30px 0 6px}
.news p{margin-bottom:7px}
.events{left:372px;width:172px;padding:16px 0 0 10px}
.events p{margin-bottom:5px}
.calendar{position:absolute;left:560px;top:65px;width:151px;height:150px;background:var(--cal-dark);border-radius:4px;overflow:hidden;font-size:8px;color:#d6d6d6}
.cal-top{height:26px;background:var(--green);color:var(--white);display:flex;align-items:center;justify-content:space-between;padding:0 8px;font-size:8.5px}
.cal-days,.cal-grid{display:grid;grid-template-columns:repeat(7,1fr);text-align:center}
.cal-days{height:16px;line-height:16px;background:var(--cal-head);color:#e6e6e6;font-size:7.5px}
.cal-grid{padding:4px 3px 0}
.cal-grid span{height:18px;line-height:18px}
.cal-grid .off{color:#777}
.cal-grid .today{background:var(--green);color:var(--white);border-radius:3px;margin:1px 2px}
.footer{position:absolute;left:0;top:1014px;width:809px;height:186px;background:var(--footer);color:#f0f0f0;font-size:11.5px;border-radius:4px 4px 0 0}
.footer ul{list-style:none;position:absolute}
.main-links{left:42px;top:18px}
.main-links li{height:19.5px}
.help-links{left:358px;top:20px}
.help-links li{height:24.8px}
.footer .site{position:absolute;left:0;right:0;top:162px;text-align:center;font-size:11.5px}
</style>
</head>
<body>
<header class="hero" role="img" aria-label="Team photo of smiling business people in suits in a bright office">
  <div class="brand"><span class="brand-mark"></span><span class="brand-name">vestolia</span></div>
  <form class="login">
    <h2>Welcome</h2>
    <div class="field">Username</div>
    <div class="field pass">••••••••</div>
    <div class="signin">Sign in</div>
    <div class="login-foot"><span>Remember me</span><span>I forgot!</span></div>
  </form>
</header>

<nav class="nav">
  <a class="active" href="#">Home</a>
  <a href="#" style="left:276px">Purchase</a>
  <a href="#" style="left:430px">Applications</a>
  <a href="#" style="left:582px">Benefits</a>
  <a href="#" style="left:736px">Support</a>
</nav>

<section class="welcome">
  <h1>Welcome to Vestolia!</h1>
  <p>Vestolia is a International company which offers softwares and solutions to IT sector companies which mainly produce Open Source softwares and offer software and consult soltuions. Vestolia is a International company which offers softwares and solutions to IT sector companies which mainly produce Open Source softwares and offer software and consult soltuions.Vestolia is a International company which offers softwares and solutions to IT sector companies which mainly produce Open Source softwares and offer software and consult soltuions.</p>
  <p>Vestolia is a International company which offers softwares and solutions to IT sector companies which mainly produce Open Source softwares and offer software and consult soltuions. Vestolia is a International company which offers softwares and solutions to IT sector companies which mainly produce Open Source softwares and offer software and consult soltuions.Vestolia is a International company which offers softwares and solutions to IT sector companies which mainly produce Open Source softwares and offer software and consult soltuions.</p>
  <p>Vestolia is a International company which offers softwares and solutions to IT sector companies which mainly produce Open Source softwares and offer software and consult soltuions. Vestolia is a International company which offers softwares and solutions to IT sector companies which mainly produce Open Source softwares and offer software and consult soltuions.Vestolia is a International company which offers softwares and solutions to IT sector companies which mainly produce Open Source softwares and offer software and consult soltuions.</p>
</section>

<section class="feeds">
  <h2 style="left:167px">News</h2>
  <h2 style="left:558px">Events Calender</h2>
  <div class="divider"></div>
  <div class="card news">
    <p>Today CEO has just annouced the Academic Status and turnover which was boosted to peaks from it basic.</p>
    <p>Today CEO has just annouced the Academic Status and turnover which was boosted to peaks from it basic.</p>
    <div class="scroll"></div>
  </div>
  <div class="card events">
    <p>9-Apri-2013<br>&gt; Company Inaguration Day</p>
    <p>9-Apri-2013<br>&gt; Company Inaguration Day</p>
    <p>9-Apri-2013<br>&gt; Company Inaguration Day</p>
    <div class="scroll"></div>
  </div>
  <div class="calendar">
    <div class="cal-top">
      <svg width="9" height="10" viewBox="0 0 9 10"><path d="M8 0 0 5 8 10Z" fill="#fff"/></svg>
      <span>April 2013</span>
      <svg width="9" height="10" viewBox="0 0 9 10"><path d="M1 0 9 5 1 10Z" fill="#fff"/></svg>
    </div>
    <div class="cal-days"><span>Sun</span><span>Mon</span><span>Tue</span><span>Wed</span><span>Thu</span><span>Fri</span><span>Sat</span></div>
    <div class="cal-grid">
      <span class="off">31</span><span>1</span><span>2</span><span>3</span><span>4</span><span>5</span><span>6</span>
      <span>7</span><span>8</span><span class="today">9</span><span>10</span><span>11</span><span>12</span><span>13</span>
      <span>14</span><span>15</span><span>16</span><span>17</span><span>18</span><span>19</span><span>20</span>
      <span>21</span><span>22</span><span>23</span><span>24</span><span>25</span><span>26</span><span>27</span>
      <span>28</span><span>29</span><span>30</span><span class="off">1</span><span class="off">2</span><span class="off">3</span><span class="off">4</span>
    </div>
  </div>
</section>

<footer class="footer">
  <ul class="main-links">
    <li>* Home page</li>
    <li>* Benefits: value of vestolia</li>
    <li>* Applications: applications offered by vestolia</li>
    <li>* Pricing</li>
    <li>* Purchase</li>
    <li>* Customer log in</li>
    <li>* Support</li>
  </ul>
  <ul class="help-links">
    <li>- FAQ</li>
    <li>- Knowledge base</li>
    <li>- Forums</li>
    <li>- Open tickets</li>
  </ul>
  <div class="site">www.vestolia.net</div>
</footer>
</body>
</html>
```